Business Card Design for Vandel Holdings

I need a business card designed for Vandel Holdings. I would like basic contact info and would like the card to be a bit modern but not childish. We manage several companies so it needs to look very professional. Watermark is cool and a plan logo maybe offset on the other side but I will leave the design up to you. I would like to see both color and grey scale designs. This is my first time using Pixel Harbor so hopefully we get some great results! Future projects available for the selected designer potentially.

Target Market(s)

Vandel Holdings owns several companies serving the software, real estate and automotive industry

Industry/Entity Type

Business

Contact Information for Business Card

Douglas R. Vandel
208.562.1437
douglas.r.vandel@mailnest.test

Font styles to use
Serif

Requirements
Must have
• contact information listed on card details
Nice to have
• I am open to letting you use your creative mind to design the best eye catching cards.

```html
<!DOCTYPE html>
<html lang="en">
<head>
<meta charset="utf-8">
<title>Vandel Holdings – Business Card</title>
<link rel="stylesheet" href="https://fonts.googleapis.com/css2?family=Arimo:wght@400;700&display=swap">
<style>
  :root {
    --stage: #2b2b2b;
    --brand-blue: #0a9fd6;
    --brand-blue-deep: #0891c4;
    --paper: #f4f5f6;
    --ink: #111418;
    --white: #ffffff;
  }
  * { box-sizing: border-box; margin: 0; padding: 0; }
  html, body { width: 1200px; height: 873px; overflow: hidden; }
  body {
    background: var(--stage);
    font-family: "Arimo", Arial, sans-serif;
    position: relative;
  }
  .card {
    position: absolute;
    width: 525px;
    height: 300px;
    border-radius: 4px;
    overflow: hidden;
    box-shadow: 0 10px 30px rgba(0,0,0,.45);
  }

  /* Back side */
  .card--back {
    left: 70px; top: 110px;
    background: linear-gradient(160deg, var(--brand-blue), var(--brand-blue-deep));
    display: flex; align-items: center; justify-content: center; gap: 18px;
  }
  .brand-dot {
    width: 54px; height: 54px; border-radius: 50%;
    border: 6px solid var(--white);
  }
  .brand-name {
    font-weight: 700; font-size: 34px; color: var(--white);
    letter-spacing: .5px;
  }

  /* Front side */
  .card--front {
    left: 605px; top: 460px;
    background: var(--paper);
  }
  .front__strip {
    position: absolute; left: 0; top: 42px;
    width: 30px; height: 222px;
    background: var(--brand-blue);
    border-radius: 0 10px 10px 0;
  }
  .front__brand {
    position: absolute; left: 44px; top: 0; width: 210px; height: 300px;
    display: flex; flex-direction: column; align-items: center; justify-content: center; gap: 12px;
  }
  .front__brand .brand-dot { border-color: var(--brand-blue); width: 46px; height: 46px; border-width: 5px; }
  .front__brand .brand-name { color: var(--brand-blue); font-size: 26px; text-align: center; line-height: 1.15; }

  .front__panel {
    position: absolute; left: 270px; top: 36px;
    width: 255px; height: 200px;
    background: var(--brand-blue);
    border-radius: 12px 0 0 12px;
    padding: 28px 18px 0 22px;
    color: var(--ink);
  }
  .contact__name {
    font-weight: 700; font-size: 17px; text-transform: uppercase; letter-spacing: .3px;
  }
  .contact__role { color: var(--white); font-size: 12px; margin-top: 3px; }
  .contact__list { list-style: none; margin-top: 30px; }
  .contact__item {
    display: flex; align-items: center; gap: 8px;
    font-size: 12.5px; margin-bottom: 14px; white-space: nowrap;
  }
  .contact__icon { width: 13px; height: 13px; flex: none; }
</style>
</head>
<body>
  <section class="card card--back" aria-label="Business card, back">
    <span class="brand-dot"></span>
    <span class="brand-name">Vandel Holdings</span>
  </section>

  <section class="card card--front" aria-label="Business card, front">
    <div class="front__strip"></div>
    <div class="front__brand">
      <span class="brand-dot"></span>
      <span class="brand-name">Vandel<br>Holdings</span>
    </div>
    <div class="front__panel">
      <h1 class="contact__name">Douglas R. Vandel</h1>
      <p class="contact__role">Managing Partner</p>
      <ul class="contact__list">
        <li class="contact__item">
          <svg class="contact__icon" viewBox="0 0 16 16" aria-hidden="true">
            <circle cx="8" cy="8" r="8" fill="#111418"/>
            <path d="M4.5 6.5c0-1 1-1.6 3.5-1.6s3.5.6 3.5 1.6l-1.3.4-.4-.9H6.2l-.4.9zM5.5 8h5l.6 3H4.9z" fill="#fff"/>
          </svg>
          <span>208.562.1437</span>
        </li>
        <li class="contact__item">
          <svg class="contact__icon" viewBox="0 0 16 16" aria-hidden="true">
            <circle cx="8" cy="8" r="8" fill="#111418"/>
            <rect x="4" y="5.2" width="8" height="5.6" fill="#fff"/>
            <path d="M4 5.2l4 3 4-3" fill="none" stroke="#111418" stroke-width=".9"/>
          </svg>
          <span>douglas.r.vandel@mailnest.test</span>
        </li>
      </ul>
    </div>
  </section>
</body>
</html>
```